Website design for lighting products company

We want a design for our website. The website is for a company that sells lighting products. The structure is similar to the below website. We really like their design as well: www.palvenorlighting.com

Industry/Entity Type

Lighting

Number of Pages Required

5+ page

Colors

Designer to choose colors to be used in the design.

Requirements
Must have
• Simple design

```html
<!DOCTYPE html>
<html lang="en">
<head>
<meta charset="utf-8">
<title>Lumora Lighting</title>
<link href="https://fonts.googleapis.com/css2?family=Montserrat:wght@400;500;600;700&display=swap" rel="stylesheet">
<style>
:root{
  --ink:#111;
  --text:#333;
  --white:#fff;
  --muted:#ececec;
  --footer:#1c1718;
  --line:#555;
  --hero-b:#2e2e2e;
}
*{box-sizing:border-box;margin:0;padding:0}
html,body{width:1200px;height:2648px;overflow:hidden}
body{font-family:'Montserrat',sans-serif;color:var(--text);background:var(--white);position:relative}
.abs{position:absolute}
section,header,footer{position:relative;width:1200px}
/* header */
.site-header{height:133px}
.logo{left:75px;top:50px;font-size:31px;font-weight:700;color:var(--ink);white-space:nowrap}
.phone{left:350px;top:26px;font-size:22px;font-weight:500;color:var(--ink);white-space:nowrap}
.social-dot{width:32px;height:32px;border-radius:50%;background:var(--ink);color:var(--white);font-size:9px;font-weight:600;display:flex;align-items:center;justify-content:center}
.signin{left:731px;top:32px;font-size:16px;color:var(--ink)}
.search{left:792px;top:30px;width:168px;height:31px;border:1px solid var(--ink);border-radius:2px;font-size:15px;color:var(--ink);display:flex;align-items:center;padding-left:12px;gap:10px}
.cta{left:967px;top:30px;width:158px;height:31px;background:var(--ink);color:var(--white);font-size:15px;display:flex;align-items:center;justify-content:center}
.nav a{position:absolute;top:87px;font-size:14px;color:var(--ink);text-decoration:none;letter-spacing:.3px}
.nav-active{left:629px;top:124px;width:54px;height:2px;background:var(--ink)}
.cart{left:1024px;top:76px;width:103px;height:30px;border:1px solid var(--ink);border-radius:2px;font-size:13px;display:flex;align-items:center;padding-left:12px;gap:8px;color:var(--ink)}
/* hero */
.hero{height:555px;background:radial-gradient(ellipse at 50% 60%,#6e6e6b,var(--hero-b) 85%)}
.hero-title{left:0;width:1200px;top:135px;text-align:center;font-size:51px;font-weight:700;color:var(--white)}
.hero-sub{left:0;width:1200px;top:200px;text-align:center;font-size:14px;color:var(--white)}
.btn{background:var(--ink);color:var(--white);font-weight:700;font-size:14px;border-radius:24px;display:flex;align-items:center;justify-content:center}
.hero-btn{left:523px;top:245px;width:154px;height:46px}
.hero-arrows{left:570px;top:490px}
/* headings */
.section-title{left:0;width:1200px;text-align:center;font-size:28px;font-weight:700;color:var(--ink)}
.title-rule{left:577px;width:46px;height:2px;background:var(--ink)}
/* welcome */
.welcome{height:455px}
.welcome-photo{left:92px;top:114px;width:481px;height:278px;background:#fff;box-shadow:0 0 4px rgba(0,0,0,.3);padding:3px}
.welcome-photo div{width:100%;height:100%;background:linear-gradient(160deg,#f1f0ea,#c8c6bd 55%,#55504c)}
.welcome-copy{left:623px;top:134px;width:515px;font-size:14px;line-height:28px}
.welcome-copy p+p{margin-top:28px}
/* arrivals */
.arrivals{height:500px}
.product{width:258px;text-align:center;top:99px}
.product-photo{height:234px}
.product h3{font-size:18px;font-weight:700;color:var(--ink);margin-top:16px;letter-spacing:.3px}
.product .price{font-size:14px;margin-top:6px}
.product .btn{width:155px;height:46px;margin:14px auto 0}
/* blog */
.blog{height:591px;background:var(--muted)}
.post{width:332px;top:132px}
.post-photo{height:188px}
.post h3{font-size:19px;font-weight:700;color:var(--ink);margin-top:24px}
.post .byline{font-size:13px;margin-top:10px}
.post p.body{font-size:14px;line-height:28px;margin-top:14px}
/* footer */
.site-footer{height:414px;background:var(--footer);color:var(--white)}
.f-head{top:84px;font-size:20px}
.field{background:#fff;color:#333;font-size:14px;display:flex;align-items:center;padding-left:15px;border-radius:2px;height:41px}
.signup{left:355px;top:178px;width:121px;height:41px;border:1px solid #aaa;font-size:14px;display:flex;align-items:center;justify-content:center;border-radius:2px}
.f-list{top:132px;font-size:16px;line-height:28px;list-style:none}
.f-social{width:32px;height:32px;border:1px solid #ddd;border-radius:50%;font-size:9px;display:flex;align-items:center;justify-content:center}
.f-logo{right:74px;top:195px;font-size:31px;font-weight:700;white-space:nowrap}
.f-rule{left:60px;top:308px;width:1080px;height:1px;background:var(--line)}
.copyright{left:74px;top:331px;font-size:12px}
.tagline{right:74px;top:325px;font-size:12px}
.pay{top:358px;width:42px;height:28px;background:#fff;color:#222;border-radius:3px;font-size:8px;font-weight:600;display:flex;align-items:center;justify-content:center}
</style>
</head>
<body>

<header class="site-header">
  <div class="abs logo">Lumora Lighting</div>
  <div class="abs phone">1-800-555-0147</div>
  <div class="abs social-dot" style="left:550px;top:26px">Fe</div>
  <div class="abs social-dot" style="left:595px;top:26px">Ch</div>
  <div class="abs social-dot" style="left:639px;top:26px">Pi</div>
  <div class="abs social-dot" style="left:682px;top:26px">Sn</div>
  <div class="abs signin">Sign in</div>
  <div class="abs search">
    <svg width="14" height="14" viewBox="0 0 14 14"><circle cx="6" cy="6" r="4.5" fill="none" stroke="#111" stroke-width="2"/><line x1="9.3" y1="9.3" x2="13" y2="13" stroke="#111" stroke-width="2"/></svg>Search
  </div>
  <div class="abs cta">GET STARTED</div>
  <nav class="nav">
    <a style="left:632px">HOME</a>
    <a style="left:713px">PRODUCTS</a>
    <a style="left:830px">BLOG</a>
    <a style="left:905px">CONTACT US</a>
  </nav>
  <div class="abs nav-active"></div>
  <div class="abs cart">CART
    <svg width="26" height="26" viewBox="0 0 26 26"><path d="M4 9h15l-1 13H5z" fill="none" stroke="#111" stroke-width="1.3"/><path d="M8 9V6a3.5 3.5 0 0 1 7 0v3" fill="none" stroke="#111" stroke-width="1.3"/><circle cx="21" cy="21" r="4.5" fill="#111"/><text x="21" y="23.5" font-size="7" fill="#fff" text-anchor="middle" font-family="Montserrat,sans-serif">0</text></svg>
  </div>
</header>

<section class="hero" role="img" aria-label="Technician installing a ceiling light panel in an office ceiling">
  <div class="abs hero-title">Lumora Lighting</div>
  <div class="abs hero-sub">Suspendisse metus adipiscing. Cras fames dapibus. Vestibulum sit</div>
  <div class="abs btn hero-btn">READ MORE</div>
  <svg class="abs hero-arrows" width="60" height="66" viewBox="0 0 60 66"><path d="M14 14l-6 6 6 6" fill="none" stroke="#fff" stroke-width="2.5"/><line x1="30" y1="0" x2="30" y2="66" stroke="#fff" stroke-width="1.5"/><path d="M46 14l6 6-6 6" fill="none" stroke="#fff" stroke-width="2.5"/></svg>
</section>

<section class="welcome">
  <h2 class="abs section-title" style="top:40px">Welcome Lumora Lighting</h2>
  <div class="abs title-rule" style="top:85px"></div>
  <div class="abs welcome-photo"><div role="img" aria-label="Modern kitchen with pendant lights over an island"></div></div>
  <div class="abs welcome-copy">
    <p>Lorem ipsum dolor sit amet, consectetur adipiscing elit, sed do eiusmod tempor incididunt ut labore et dolore magna aliqua. Ut enim ad minim veniam, quis nostrud exercitation ullamco laboris nisi ut aliquip ex ea commodo consequat. Duis aute irure dolor in reprehenderit in voluptate velit esse.</p>
    <p>Sed ut perspiciatis unde omnis iste natus error sit voluptatem accusantium doloremque laudantium, totam rem.</p>
  </div>
</section>

<section class="arrivals">
  <h2 class="abs section-title" style="top:2px">New Arrivals</h2>
  <div class="abs title-rule" style="top:47px"></div>
  <div class="abs product" style="left:60px"><div class="product-photo" role="img" aria-label="Bright modern office interior" style="background:linear-gradient(160deg,#d9dadc,#f3f3f3 50%,#9a8f84)"></div><h3>INDOOR LIGHTS</h3><div class="price">from ($30.00)</div><div class="btn">ADD TO CART</div></div>
  <div class="abs product" style="left:334px"><div class="product-photo" role="img" aria-label="Glowing filament bulb outdoors at night" style="background:radial-gradient(circle at 30% 40%,#c0742a,#2a2a1a 40%,#121712)"></div><h3>OUT DOOR LIGHTS</h3><div class="price">from ($30.00)</div><div class="btn">ADD TO CART</div></div>
  <div class="abs product" style="left:607px"><div class="product-photo" role="img" aria-label="Corridor with emergency exit sign" style="background:linear-gradient(100deg,#d6d6d6,#8a7a6a 45%,#3a342e)"></div><h3>EMERGENCY LIGHTS</h3><div class="price">from ($30.00)</div><div class="btn">ADD TO CART</div></div>
  <div class="abs product" style="left:882px"><div class="product-photo" role="img" aria-label="Man adjusting kitchen lighting with a tablet" style="background:linear-gradient(160deg,#e8e8e6,#c8c4b8 60%,#3a4a6a)"></div><h3>LIGHTING CONTROLS</h3><div class="price">from ($30.00)</div><div class="btn">ADD TO CART</div></div>
</section>

<section class="blog">
  <h2 class="abs section-title" style="top:55px">Blog</h2>
  <div class="abs title-rule" style="top:107px"></div>
  <article class="abs post" style="left:74px"><div class="post-photo" role="img" aria-label="Warm glowing light bulbs by a window" style="background:linear-gradient(90deg,#c9c4b8,#e8a860 60%,#b8702a)"></div><h3>Sed ut perspiciatis unde omnis</h3><div class="byline">by Mara Ellison December 16, 2019</div><p class="body">Sed ut perspiciatis unde omnis iste natus error sit voluptatem accusantium doloremque laudantium, totam rem aperiam, eaque ipsa quae ab illo inventore veritatis</p></article>
  <article class="abs post" style="left:435px"><div class="post-photo" role="img" aria-label="Street lamp against blue sky and glass building" style="background:linear-gradient(120deg,#9cc4ec,#3c78d0 60%,#1a3c9c)"></div><h3>Sed ut perspiciatis unde omnis</h3><div class="byline">by Mara Ellison December 16, 2019</div><p class="body">Sed ut perspiciatis unde omnis iste natus error sit voluptatem accusantium doloremque laudantium, totam rem aperiam, eaque ipsa quae ab illo inventore veritatis</p></article>
  <article class="abs post" style="left:796px"><div class="post-photo" role="img" aria-label="Hand pressing a wall lighting control panel" style="background:linear-gradient(90deg,#4a4a4a,#6a6660 50%,#c89850)"></div><h3>Sed ut perspiciatis unde omnis</h3><div class="byline">by Mara Ellison December 16, 2019</div><p class="body">Sed ut perspiciatis unde omnis iste natus error sit voluptatem accusantium doloremque laudantium, totam rem aperiam, eaque ipsa quae ab illo inventore veritatis</p></article>
</section>

<footer class="site-footer">
  <div class="abs f-head" style="left:74px">Sign up for our Newsletter</div>
  <div class="abs field" style="left:74px;top:122px;width:197px">First name</div>
  <div class="abs field" style="left:279px;top:122px;width:197px">Last name</div>
  <div class="abs field" style="left:74px;top:178px;width:271px">Email Address</div>
  <div class="abs signup">SIGN UP</div>

  <div class="abs f-head" style="left:499px">Company</div>
  <ul class="abs f-list" style="left:500px"><li>Home</li><li>About Us</li><li>Products</li><li>Blog</li><li>Contact Us</li></ul>

  <div class="abs f-head" style="left:721px">Communities</div>
  <ul class="abs f-list" style="left:721px"><li>Event</li><li>Testimonials</li><li>Sitemap</li></ul>

  <div class="abs f-head" style="left:929px">Social</div>
  <div class="abs f-social" style="left:926px;top:131px">Fe</div>
  <div class="abs f-social" style="left:971px;top:131px">Ch</div>
  <div class="abs f-social" style="left:1015px;top:131px">Pi</div>
  <div class="abs f-social" style="left:1058px;top:131px">Sn</div>
  <div class="abs f-logo">Lumora Lighting</div>

  <div class="abs f-rule"></div>
  <div class="abs copyright">copyright 2019 &nbsp;|&nbsp; www.companyname.com</div>
  <div class="abs tagline">Quis nostrum exercitationem ullam corporis</div>
  <div class="abs pay" style="left:828px">Cardwell</div>
  <div class="abs pay" style="left:879px">Ringpay</div>
  <div class="abs pay" style="left:931px">Corvex</div>
  <div class="abs pay" style="left:982px">Paylo</div>
  <div class="abs pay" style="left:1033px">Dinara</div>
  <div class="abs pay" style="left:1085px">Orbis</div>
</footer>

</body>
</html>
```